Profesional personal website needs design and business card

I need a business card with my professional name as a logo "Dorian Vitality" for my business. I am a Wellness Coach, consultant and trainer. So it should be professional, wellness oriented and modern.

Target Market(s)

Private clients, governments, corporations. Luxury and high market.

Industry/Entity Type

Health And Wellness

Contact Information for Business Card

Dorian Vitality should be the logo

Colors

Designer to choose colors to be used in the design.

Requirements
Must have
• Dorian Vitality
• Name: Tomás Lirandel
• Wellness Coach, Consultant & Trainer.
• Website: www.dorianvitality-example.com
• Phone:
• Spain (+34) 612 480 317
• (USA) +1 (555) 610 4829
Nice to have
• The most important is the design of "Dorian Vitality", as this is going to be my personal brand logo. It should be professional, wellness, high end and actual.
Should not have
• no golds, no baroque style..

```html
<!DOCTYPE html>
<html lang="en">
<head>
<meta charset="utf-8">
<title>Dorian Vitality – Business Card</title>
<link href="https://fonts.googleapis.com/css2?family=Questrial&family=Arimo:wght@400&display=swap" rel="stylesheet">
<style>
  :root {
    --backdrop: #c4c4c4;
    --charcoal: #3a3a3a;
    --ink: #333333;
    --green: #6aaa0c;
    --paper: #ffffff;
  }
  * { margin: 0; padding: 0; box-sizing: border-box; }
  html, body {
    width: 1200px; height: 802px; overflow: hidden;
    background: var(--backdrop);
  }
  .canvas { position: relative; width: 1200px; height: 802px; }

  .card {
    position: absolute; top: 274px;
    width: 443px; height: 264px;
  }

  /* Front */
  .card-front { left: 136px; background: var(--paper); }
  .card-front .side-band {
    position: absolute; left: 0; top: 0; bottom: 0;
    width: 50px; background: var(--charcoal);
  }
  .card-front .side-accent {
    position: absolute; left: 50px; top: 0; bottom: 0;
    width: 4px; background: var(--green);
  }
  .brand-front {
    position: absolute; right: 26px; top: 86px;
    display: flex; align-items: center; gap: 9px;
  }
  .brand-mark {
    width: 14px; height: 14px; border-radius: 50%;
    background: var(--green);
  }
  .brand-name {
    font-family: "Questrial", sans-serif;
    font-size: 25px; line-height: 1;
    color: var(--ink); white-space: nowrap;
  }
  .holder {
    position: absolute; left: 67px; top: 147px;
  }
  .holder-name {
    font-family: "Questrial", sans-serif;
    font-size: 18.5px; font-weight: 400; color: var(--ink);
    line-height: 1;
  }
  .holder-name .surname { color: var(--green); }
  .holder-role {
    font-family: "Arimo", sans-serif;
    font-size: 12.5px; color: var(--ink);
    margin-top: 5px;
  }
  .contacts {
    list-style: none; margin-top: 14px;
    font-family: "Arimo", sans-serif; font-size: 12.5px; color: var(--ink);
  }
  .contacts li {
    display: flex; align-items: center; gap: 3px;
    height: 15.5px;
  }
  .contacts svg { width: 14px; height: 14px; flex: none; }
  .contacts .region { color: var(--green); margin-left: 4px; }
  .contacts .region.tight { margin-left: 0; }

  /* Back */
  .card-back { left: 624px; background: var(--charcoal); }
  .brand-back {
    position: absolute; left: 0; right: 0; top: 0; bottom: 0;
    display: flex; align-items: center; justify-content: center; gap: 14px;
  }
  .brand-back .brand-mark { width: 22px; height: 22px; }
  .brand-back .brand-name { font-size: 38px; color: var(--paper); }
</style>
</head>
<body>
<main class="canvas">

  <section class="card card-front" aria-label="Business card front">
    <div class="side-band"></div>
    <div class="side-accent"></div>

    <div class="brand-front">
      <span class="brand-mark"></span>
      <span class="brand-name">Dorian Vitality</span>
    </div>

    <div class="holder">
      <h1 class="holder-name">Tomás <span class="surname">Lirandel</span></h1>
      <p class="holder-role">Wellness Coach, Consultant &amp; Trainer</p>
      <ul class="contacts">
        <li>
          <svg viewBox="0 0 14 14" aria-hidden="true"><circle cx="7" cy="7" r="6.2" fill="none" stroke="#6aaa0c" stroke-width="1.2"/><path d="M4.6 3.8c.4-.3.8-.2 1 .2l.6 1.1c.2.3.1.6-.2.8l-.4.3c.3.9 1 1.6 1.9 2l.3-.4c.2-.3.5-.4.8-.2l1.1.6c.4.2.5.6.2 1-.5.7-1.2 1-2 .7C6 9.4 4.6 8 4 6.1c-.3-.9 0-1.7.6-2.3z" fill="#6aaa0c"/></svg>
          (+34) 612 480 317<span class="region">(SPAIN)</span>
        </li>
        <li>
          <svg viewBox="0 0 14 14" aria-hidden="true"><circle cx="7" cy="7" r="6.2" fill="none" stroke="#6aaa0c" stroke-width="1.2"/><path d="M4.6 3.8c.4-.3.8-.2 1 .2l.6 1.1c.2.3.1.6-.2.8l-.4.3c.3.9 1 1.6 1.9 2l.3-.4c.2-.3.5-.4.8-.2l1.1.6c.4.2.5.6.2 1-.5.7-1.2 1-2 .7C6 9.4 4.6 8 4 6.1c-.3-.9 0-1.7.6-2.3z" fill="#6aaa0c"/></svg>
          +1 (555) 610 4829<span class="region tight">(USA)</span>
        </li>
        <li>
          <svg viewBox="0 0 14 14" aria-hidden="true"><g fill="none" stroke="#6aaa0c" stroke-width="1.1"><circle cx="7" cy="7" r="6"/><ellipse cx="7" cy="7" rx="2.6" ry="6"/><path d="M1 7h12M2 4h10M2 10h10"/></g></svg>
          www.dorianvitality-example.com
        </li>
      </ul>
    </div>
  </section>

  <section class="card card-back" aria-label="Business card back">
    <div class="brand-back">
      <span class="brand-mark"></span>
      <span class="brand-name">Dorian Vitality</span>
    </div>
  </section>

</main>
</body>
</html>
```